RWT Fittings Ltd Business Cards

We need a business card with our business logo. We provide window and door installations on high-rises in west coast British Colombia, Canada.

I would like my business information and details on one side of the card, and the other side the company name with logo

Target Market(s)

General Contractors

Industry/Entity Type

Construction

Contact Information for Business Card

one side i want my company name and logo in the dark theme logo that i provided

Requirements
Must have
• Marco Peltieri, 16045518293, RWTFittings@mailbox-demo.com, 1407-5194 Linden Row Burnaby BC, V5H 2K9, Owner & Manager

```html
<!DOCTYPE html>
<html lang="en">
<head>
<meta charset="utf-8">
<title>RWT Fittings Ltd – Business Cards</title>
<link href="https://fonts.googleapis.com/css2?family=Barlow:wght@500&family=Montserrat:wght@500;600&family=Russo+One&display=swap" rel="stylesheet">
<style>
  :root {
    --backdrop: #e6e7e9;
    --card-light: #ffffff;
    --card-dark: #2c2b2d;
    --brand-blue: #3aaee2;
    --brand-grey: #9a9a9c;
    --ink: #3a3a3c;
  }
  html, body {
    margin: 0;
    padding: 0;
    width: 1200px;
    height: 1000px;
    overflow: hidden;
    background: var(--backdrop);
  }
  .canvas {
    position: relative;
    width: 1200px;
    height: 1000px;
  }
  .card {
    position: absolute;
    left: 303px;
    width: 592px;
    height: 338px;
    box-sizing: border-box;
  }
  .card--front {
    top: 108px;
    background: var(--card-light);
  }
  .card--back {
    top: 552px;
    background: var(--card-dark);
    overflow: hidden;
  }

  /* wordmark */
  .wordmark {
    position: absolute;
    display: flex;
    align-items: center;
    gap: 12px;
    font-family: "Montserrat", sans-serif;
    font-weight: 600;
    color: var(--brand-blue);
    white-space: nowrap;
  }
  .wordmark__square {
    background: var(--brand-grey);
    flex: none;
  }
  .card--front .wordmark {
    left: 42px;
    top: 56px;
    font-size: 30px;
  }
  .card--front .wordmark__square {
    width: 44px;
    height: 44px;
  }

  /* contact block */
  .contact {
    position: absolute;
    right: 42px;
    top: 124px;
    text-align: right;
    font-family: "Barlow", sans-serif;
    font-weight: 500;
    font-size: 14.5px;
    color: var(--ink);
    line-height: 19px;
  }
  .contact p { margin: 0; }
  .contact .contact__phone { margin-top: 7px; }
  .contact .contact__email { margin-top: 6px; }

  .divider {
    position: absolute;
    left: 42px;
    right: 42px;
    top: 229px;
    height: 3px;
    background-image: radial-gradient(circle, var(--brand-blue) 1.4px, transparent 1.6px);
    background-size: 8.1px 3px;
    background-repeat: repeat-x;
  }

  .person {
    position: absolute;
    left: 42px;
    top: 240px;
  }
  .person__name {
    margin: 0;
    font-family: "Russo One", sans-serif;
    font-weight: 400;
    font-size: 31px;
    letter-spacing: 0.5px;
    color: var(--brand-blue);
    line-height: 36px;
  }
  .person__role {
    margin: 2px 0 0;
    font-family: "Montserrat", sans-serif;
    font-weight: 500;
    font-size: 18px;
    color: var(--brand-grey);
  }

  /* back */
  .backdrop-art {
    position: absolute;
    inset: 0;
    background: linear-gradient(100deg, #242325 0%, #333235 45%, #3e3d40 80%, #2a292b 100%);
  }
  .card--back .wordmark {
    left: 50%;
    top: 50%;
    transform: translate(-50%, -50%);
    font-size: 34px;
    gap: 14px;
  }
  .card--back .wordmark__square {
    width: 50px;
    height: 50px;
  }
</style>
</head>
<body>
<main class="canvas">
  <section class="card card--front" aria-label="Business card front">
    <div class="wordmark">
      <span class="wordmark__square" aria-hidden="true"></span>
      <span class="wordmark__name">RWT Fittings Ltd</span>
    </div>

    <div class="contact">
      <p>1407-5194 Linden Row</p>
      <p>Burnaby BC, V5H 2K9</p>
      <p class="contact__phone">+1-604-551-8293</p>
      <p class="contact__email">RWTFittings@mailbox-demo.com</p>
    </div>

    <div class="divider" aria-hidden="true"></div>

    <div class="person">
      <h1 class="person__name">MARCO PELTIERI</h1>
      <p class="person__role">Owner &amp; Manager</p>
    </div>
  </section>

  <section class="card card--back" aria-label="Business card back">
    <div class="backdrop-art" role="img" aria-label="Large faint dark-grey building silhouette decoration"></div>
    <div class="wordmark">
      <span class="wordmark__square" aria-hidden="true"></span>
      <span class="wordmark__name">RWT Fittings Ltd</span>
    </div>
  </section>
</main>
</body>
</html>
```